Falkrin homes and renovations business card design.

Would like some new card designs utilizing my new logo that look professional. I am open to different colors on the logo or utilize the same ones we have. I like the original concept but would like to see some fresh ideas and build on what we have already done.

Target Market(s)

Custom home building industry, Real estate sales, Renovation projects.

Industry/Entity Type

Home Builder

Contact Information for Business Card

Falkrin Homes and Renovations
2871 96th Avenue
Kestrow, Valdora
T2R3W8
Home : 403- 718-4063 Cell: 403- 294-5170

My info is : Dax Falkrin, President and CEO
email: falkrinhomes@maildrop-example.net
Website: falkrinhomes-example.com
websit

Requirements
Must have
• Must Use my new logo design. I am open to different colors on the logo or utilize the same ones in the existing design. I can upload the original logo design if needed.

```html
<!DOCTYPE html>
<html lang="en">
<head>
<meta charset="utf-8">
<title>Falkrin Homes and Renovations – Business Card</title>
<link rel="stylesheet" href="https://fonts.googleapis.com/css2?family=Montserrat:wght@300;400;500;700&display=swap">
<style>
  :root {
    --page-bg: #c9cacc;
    --card-bg: #3e3e40;
    --accent-yellow: #f5bd1f;
    --brand-gold: #b5862e;
    --text-light: #ffffff;
    --icon-dark: #3e3e40;
  }
  * { box-sizing: border-box; margin: 0; padding: 0; }
  html, body {
    width: 1200px; height: 800px; overflow: hidden;
    background: var(--page-bg);
    font-family: "Montserrat", Arial, sans-serif;
  }
  .canvas { position: relative; width: 1200px; height: 800px; }

  .card {
    position: absolute; left: 345px; width: 510px; height: 282px;
    background: var(--card-bg); border-radius: 16px; overflow: hidden;
  }
  .card--front { top: 70px; }
  .card--back { top: 409px; }

  .card__band { position: absolute; left: 0; bottom: 0; width: 100%; height: 19px; display: block; }

  .brand { position: absolute; text-align: center; color: var(--brand-gold); font-weight: 700; line-height: 1; }
  .brand__mark { display: inline-block; background: var(--brand-gold); }
  .brand__name { display: block; }
  .brand__tagline { display: block; }

  .card--front .brand { left: 28px; top: 112px; width: 170px; }
  .card--front .brand__mark { width: 14px; height: 14px; margin-bottom: 10px; }
  .card--front .brand__name { font-size: 28px; letter-spacing: 0.5px; }
  .card--front .brand__tagline { font-size: 9.5px; margin-top: 4px; letter-spacing: 0.2px; }

  .card--back .brand { left: 125px; top: 84px; width: 260px; }
  .card--back .brand__mark { width: 20px; height: 20px; margin-bottom: 16px; }
  .card--back .brand__name { font-size: 42px; letter-spacing: 0.8px; }
  .card--back .brand__tagline { font-size: 14px; margin-top: 6px; letter-spacing: 0.3px; }

  .divider-vertical { position: absolute; left: 233px; top: 72px; width: 3px; height: 138px; background: var(--accent-yellow); }
  .rule { position: absolute; left: 270px; width: 213px; height: 3px; background: var(--accent-yellow); }
  .rule--top { top: 73px; }
  .rule--bottom { top: 185px; }

  .person { position: absolute; left: 276px; top: 20px; width: 192px; text-align: center; color: var(--text-light); }
  .person__name { font-size: 24px; font-weight: 400; line-height: 1; letter-spacing: 0.3px; white-space: nowrap; }
  .person__title { font-size: 12.5px; font-weight: 300; line-height: 1; margin-top: 1px; white-space: nowrap; }

  .contact { position: absolute; left: 270px; color: var(--text-light); font-size: 12px; font-weight: 400; line-height: 1.3; display: flex; align-items: center; white-space: nowrap; }
  .contact__icon { width: 24px; height: 24px; border-radius: 50%; background: var(--accent-yellow); display: flex; align-items: center; justify-content: center; margin-right: 12px; flex: none; }
  .contact__icon svg { width: 14px; height: 14px; }
  .contact--phone { top: 86px; }
  .contact--email { top: 121px; }
  .contact--email .contact__text { font-size: 10px; letter-spacing: -0.1px; }
  .contact--web { top: 153px; }
  .contact--web .contact__text { font-size: 11px; }

  .address { position: absolute; left: 270px; top: 196px; color: var(--text-light); font-size: 11.5px; font-weight: 400; white-space: nowrap; }
</style>
</head>
<body>
<main class="canvas">

  <section class="card card--front" aria-label="Business card front">
    <div class="brand">
      <span class="brand__mark"></span>
      <span class="brand__name">FALKRIN</span>
      <span class="brand__tagline">HOMES AND RENOVATIONS</span>
    </div>

    <div class="divider-vertical"></div>

    <div class="person">
      <p class="person__name">Dax Falkrin</p>
      <p class="person__title">President and CEO</p>
    </div>

    <div class="rule rule--top"></div>

    <div class="contact contact--phone">
      <span class="contact__icon">
        <svg viewBox="0 0 14 14" fill="none" stroke="var(--icon-dark)" stroke-width="1.2"><rect x="4" y="1" width="6" height="12" rx="1"/><line x1="6" y1="11" x2="8" y2="11"/></svg>
      </span>
      <span class="contact__text">403- 718-4063<br>403- 294-5170</span>
    </div>

    <div class="contact contact--email">
      <span class="contact__icon">
        <svg viewBox="0 0 14 14" fill="none" stroke="var(--icon-dark)" stroke-width="1.1"><rect x="1.5" y="3" width="11" height="8"/><polyline points="1.5,3 7,8 12.5,3"/></svg>
      </span>
      <span class="contact__text">falkrinhomes@maildrop-example.net</span>
    </div>

    <div class="contact contact--web">
      <span class="contact__icon">
        <svg viewBox="0 0 14 14" fill="none" stroke="var(--icon-dark)" stroke-width="1.1"><circle cx="7" cy="7" r="5.5"/><ellipse cx="7" cy="7" rx="2.5" ry="5.5"/><line x1="1.5" y1="7" x2="12.5" y2="7"/></svg>
      </span>
      <span class="contact__text">www.falkrinhomes-example.com</span>
    </div>

    <div class="rule rule--bottom"></div>

    <p class="address">2871 96th Avenue Kestrow, Valdora</p>

    <svg class="card__band" viewBox="0 0 510 19" preserveAspectRatio="none" aria-hidden="true">
      <rect width="510" height="19" fill="var(--accent-yellow)"/>
      <line x1="252" y1="19" x2="268" y2="0" stroke="var(--card-bg)" stroke-width="3"/>
    </svg>
  </section>

  <section class="card card--back" aria-label="Business card back">
    <div class="brand">
      <span class="brand__mark"></span>
      <span class="brand__name">FALKRIN</span>
      <span class="brand__tagline">HOMES AND RENOVATIONS</span>
    </div>

    <svg class="card__band" viewBox="0 0 510 19" preserveAspectRatio="none" aria-hidden="true">
      <rect width="510" height="19" fill="var(--accent-yellow)"/>
      <line x1="252" y1="19" x2="268" y2="0" stroke="var(--card-bg)" stroke-width="3"/>
    </svg>
  </section>

</main>
</body>
</html>
```